Birchline Septic Solutions

Would like to see some single sided ones but would also like to see some double sided with one sided only being the logo. Owners name is Colin Vandro. Phone number is 555-214-0387
Services are pumping, inspections, installs, and repairs

Contact Information for Business Card

555-241-0387 Colin Vandro Fernvale, OH

```html
<!DOCTYPE html>
<html lang="en">
<head>
<meta charset="utf-8">
<title>Birchline Septic Solutions – Business Card</title>
<link rel="stylesheet" href="https://fonts.googleapis.com/css2?family=Open+Sans:wght@400;600;700;800&display=swap">
<style>
  :root {
    --teal: #27bfbb;
    --teal-deep: #1d8e8b;
    --charcoal: #222226;
    --stage: #2a2a2c;
    --white: #ffffff;
    --rule: #8a8a8e;
  }
  * { box-sizing: border-box; margin: 0; padding: 0; }
  html, body {
    width: 1200px; height: 779px; overflow: hidden;
    background: var(--stage);
    font-family: "Open Sans", Arial, sans-serif;
  }
  .canvas {
    width: 1200px; height: 779px;
    display: flex; align-items: center; justify-content: center; gap: 30px;
  }
  .card {
    width: 560px; height: 320px; position: relative; overflow: hidden;
    box-shadow: 0 10px 30px rgba(0,0,0,.5);
  }
  /* Front: logo only */
  .card--front {
    background: var(--teal);
    display: flex; align-items: center; justify-content: center;
  }
  .brand {
    display: flex; align-items: center; gap: 12px;
    color: var(--teal-deep); font-weight: 800;
    text-transform: uppercase; letter-spacing: 1px; line-height: 1.05;
  }
  .brand__mark {
    width: 18px; height: 18px; border-radius: 50%; background: currentColor; flex: none;
  }
  .card--front .brand { font-size: 34px; }
  .card--front .brand__name { text-align: left; }

  /* Back: contact side */
  .card--back { background: var(--charcoal); }
  .card--back .brand {
    position: absolute; left: 46px; top: 102px;
    color: var(--white); font-size: 21px;
  }
  .card--back .brand__mark { width: 12px; height: 12px; }
  .divider {
    position: absolute; left: 290px; top: 62px;
    width: 1px; height: 128px; background: var(--rule);
  }
  .contact { position: absolute; left: 318px; top: 78px; color: var(--white); }
  .contact__name { font-size: 28px; font-weight: 700; line-height: 1.1; }
  .contact__first { color: var(--teal); }
  .contact__line { font-size: 15px; margin-top: 6px; display: flex; align-items: center; gap: 7px; }
  .contact__line svg { width: 14px; height: 14px; flex: none; }

  .services-tag {
    position: absolute; left: 222px; top: 222px;
    background: var(--teal); color: var(--white);
    font-size: 13px; font-weight: 600; letter-spacing: .5px;
    padding: 3px 20px; border-radius: 50%;
    border: 1.5px solid var(--white);
  }
  .services-band {
    position: absolute; left: 0; right: 0; bottom: 28px; height: 40px;
    background: var(--teal);
    display: flex; align-items: center; justify-content: center; gap: 14px;
    color: var(--white); font-size: 17px;
  }
  .services-band li { list-style: none; display: flex; align-items: center; gap: 7px; }
  .services-band li::before {
    content: ""; width: 9px; height: 9px; border-radius: 50%; background: var(--white);
  }
</style>
</head>
<body>
<main class="canvas">
  <section class="card card--front" aria-label="Card front">
    <div class="brand">
      <span class="brand__mark"></span>
      <span class="brand__name">Birchline<br>Septic Solutions</span>
    </div>
  </section>

  <section class="card card--back" aria-label="Card back">
    <div class="brand">
      <span class="brand__mark"></span>
      <span class="brand__name">Birchline<br>Septic Solutions</span>
    </div>
    <div class="divider"></div>
    <div class="contact">
      <p class="contact__name"><span class="contact__first">Colin</span> Vandro</p>
      <p class="contact__line">Fernvale, OH</p>
      <p class="contact__line">
        <svg viewBox="0 0 24 24" aria-hidden="true"><path fill="#27bfbb" d="M6.6 10.8a15.1 15.1 0 0 0 6.6 6.6l2.2-2.2a1 1 0 0 1 1-.25 11.4 11.4 0 0 0 3.6.57 1 1 0 0 1 1 1V20a1 1 0 0 1-1 1A17 17 0 0 1 3 4a1 1 0 0 1 1-1h3.5a1 1 0 0 1 1 1c0 1.25.2 2.45.57 3.57a1 1 0 0 1-.25 1z"/></svg>
        555-241-0387
      </p>
    </div>
    <span class="services-tag">SERVICES</span>
    <ul class="services-band">
      <li>Pumping</li>
      <li>Inspections</li>
      <li>Installs</li>
      <li>And Repairs</li>
    </ul>
  </section>
</main>
</body>
</html>
```